STAND OUT BUSINESS CARD REQUIRED

I would like a business card that is going to be different and stand out!

Target Market(s)

Residential market, adults from 28yrs on

Industry/Entity Type

Electrician

Requirements
Must have
• Business name
• my name
• phone number
• email
• web address
• license no.
• abn
• fax no
• logo
Nice to have
• Extra info:
• FREE quotes
• Fixed pricing
• On time guarantee
• Life time labour Guarantee

```html
<!DOCTYPE html>
<html lang="en">
<head>
<meta charset="utf-8">
<title>Bright Spark – Business Card</title>
<link href="https://fonts.googleapis.com/css2?family=Nunito:wght@400;600;800;900&display=swap" rel="stylesheet">
<style>
  :root {
    --backdrop: #e9e6e2;
    --card: #231f20;
    --orange: #f7941d;
    --white: #ffffff;
    --soft-white: #e8e8e8;
  }
  * { margin: 0; padding: 0; box-sizing: border-box; }
  html, body {
    width: 1200px;
    height: 831px;
    overflow: hidden;
    background: var(--backdrop);
    font-family: "Nunito", sans-serif;
  }
  .canvas {
    position: relative;
    width: 1200px;
    height: 831px;
  }
  .card {
    position: absolute;
    width: 600px;
    height: 350px;
    background: var(--card);
    border-radius: 3px;
    box-shadow: 0 6px 18px rgba(0,0,0,0.25);
    color: var(--white);
  }
  .card--front { left: 60px; top: 40px; }
  .card--back  { left: 540px; top: 430px; }

  .holder-name {
    position: absolute;
    left: 28px; top: 44px;
    font-size: 29px;
    font-weight: 800;
    color: var(--orange);
    letter-spacing: 0.5px;
  }
  .holder-title {
    position: absolute;
    left: 28px; top: 82px;
    font-size: 17px;
    font-weight: 400;
    color: var(--soft-white);
  }
  .contact {
    position: absolute;
    left: 28px;
    display: grid;
    grid-template-columns: 100px auto;
    row-gap: 1px;
    font-size: 17px;
    line-height: 23px;
  }
  .contact--phones { top: 148px; }
  .contact--online { top: 228px; }
  .contact dt { font-weight: 800; color: var(--white); }
  .contact dd { font-weight: 400; color: var(--soft-white); }

  .brand {
    position: absolute;
    left: 370px; top: 200px;
    display: flex;
    align-items: center;
    gap: 10px;
    font-size: 26px;
    font-weight: 900;
    color: var(--orange);
    line-height: 1;
  }
  .brand-dot {
    width: 22px; height: 22px;
    border-radius: 50%;
    background: var(--orange);
  }

  .offers {
    position: absolute;
    left: 60px; top: 110px;
    text-transform: uppercase;
    font-weight: 900;
    line-height: 1.05;
  }
  .offers-line--small { font-size: 27px; color: var(--orange); }
  .offers-line--small .offers-aside { color: var(--white); font-size: 22px; }
  .offers-line--big { font-size: 45px; letter-spacing: 1px; }
  .offers-line--white { color: var(--white); }
  .offers-line--orange { color: var(--orange); }
</style>
</head>
<body>
<main class="canvas">
  <section class="card card--front" aria-label="Card front">
    <h1 class="holder-name">MARCUS REED</h1>
    <p class="holder-title">Chief Executive Director</p>

    <dl class="contact contact--phones">
      <dt>phone</dt><dd>+03 7148 2260</dd>
      <dt>mobile</dt><dd>+03 5391 0473</dd>
    </dl>
    <dl class="contact contact--online">
      <dt>email</dt><dd>mreed@voltmail.com</dd>
      <dt>web</dt><dd>brightsparkpower.com</dd>
      <dt>license #</dt><dd>4172658</dd>
    </dl>

    <div class="brand">
      <span class="brand-dot"></span>
      <span class="brand-name">BRIGHT SPARK PTY LTD</span>
    </div>
  </section>

  <section class="card card--back" aria-label="Card back">
    <div class="offers">
      <p class="offers-line offers-line--small">Free Quotes <span class="offers-aside">• Fixed pricing on time</span></p>
      <p class="offers-line offers-line--big offers-line--white">Guarantee Lifetime</p>
      <p class="offers-line offers-line--big offers-line--orange">Labour Guarantee</p>
    </div>
  </section>
</main>
</body>
</html>
```